Tarvo FrameNook

Hi There,

I am looking to rebuild my company website.

Here are the development specs for my new site!:

1) I've designed a layout for my site and am looking for someone to incorporate the graphics into a word press template. Enclosed is a screen grab of the look and feel (all of the images / graphic working files are available).

2) The site needs to be built on a wordpress platform so that I can regularly edit the site content and make changes / updates

4) The web content (text) has not been finalized and is still being created. For now, I would really like to get the site developed (from a functionality standpoint) and provide text for each page as we finalize the site development.

I'm really excited to get my site redeveloped and launched!

Industry/Entity Type

It Company

Requirements
Must have
• Home Page to have rotating images

```html
<!DOCTYPE html>
<html lang="en">
<head>
<meta charset="utf-8">
<title>Tarvo FrameNook</title>
<link href="https://fonts.googleapis.com/css2?family=Ubuntu:ital,wght@0,400;0,500;0,700;1,500;1,700&family=Oswald:wght@500&family=Bree+Serif&display=swap" rel="stylesheet">
<style>
:root{
  --ink:#2b2b2b;
  --grey-brand:#5e5e62;
  --blue-brand:#3a6fb5;
  --accent-blue:#4a7fd8;
  --magenta:#b3206a;
  --magenta-dark:#8e1752;
  --dark:#161616;
  --dark-panel:#1f1f1f;
  --nav-dark:#262626;
  --light-band:#ececec;
  --footer:#1c1c1c;
  --footer-text:#e8e8e8;
  --navy-link:#1f3a7a;
}
*{box-sizing:border-box;margin:0;padding:0}
html,body{width:726px;height:1200px;overflow:hidden;background:#fff}
body{position:relative;font-family:"Ubuntu",sans-serif;color:var(--ink)}
.abs{position:absolute}

/* header */
.site-header{position:absolute;left:0;top:0;width:726px;height:111px;background:linear-gradient(#f7f7f7,#ececec)}
.brand{position:absolute;left:35px;top:22px;display:flex;align-items:center;gap:8px}
.brand-dot{width:30px;height:30px;border-radius:50%;background:var(--blue-brand)}
.brand-name{font-family:"Ubuntu",sans-serif;font-weight:700;font-size:24px;color:var(--grey-brand);letter-spacing:-.3px}
.phone{position:absolute;left:557px;top:8px;display:flex;align-items:center;gap:5px;font-weight:500;font-size:14px;color:#333}
.nav-icons{position:absolute;left:244px;top:52px;width:430px;height:24px}
.nav-icons svg{position:absolute;top:0}
.main-nav{position:absolute;left:244px;top:78px;height:32px;display:flex;background:linear-gradient(#3a3a3a,#181818);border:1px solid #111}
.main-nav a{display:flex;align-items:center;justify-content:center;height:100%;color:#fff;text-decoration:none;font-size:9.5px;font-weight:500;border-right:1px solid #4a4a4a}
.main-nav a:last-child{border-right:0}

/* hero */
.hero-band{position:absolute;left:0;top:111px;width:726px;height:233px;background:var(--dark)}
.slider{position:absolute;left:31px;top:142px;width:640px;height:247px;background:var(--dark-panel);box-shadow:0 6px 10px rgba(0,0,0,.45)}
.slide-image{position:absolute;left:13px;top:13px;width:374px;height:211px;background:linear-gradient(135deg,#1d3b66 0%,#5a78a0 35%,#e4e6e4 55%,#c9d0cc 75%,#6f8a3a 100%)}
.slide-title{position:absolute;left:401px;top:12px;font-family:"Oswald",sans-serif;font-size:25px;color:var(--accent-blue);letter-spacing:.3px}
.slide-text{position:absolute;left:402px;top:50px;width:226px;font-size:9.6px;line-height:15.5px;color:#f2f2f2}
.know-more{position:absolute;left:402px;top:184px;width:221px;height:40px;background:linear-gradient(var(--magenta),var(--magenta-dark));display:flex;align-items:center;justify-content:center;gap:10px;font-family:"Bree Serif",serif;font-size:21px;color:#fff;letter-spacing:.5px}
.slider-dots{position:absolute;left:286px;top:234px;display:flex;gap:5px}
.slider-dots span{width:6px;height:6px;border-radius:50%;background:#888}
.slider-dots span:first-child{background:#d01f1f}

/* welcome */
.welcome-title{position:absolute;left:35px;top:405px;font-size:14px;font-weight:700;font-style:italic;color:#222}
.welcome-title em{color:#2b4aa8}
.welcome-text{position:absolute;left:35px;top:430px;width:218px;font-size:8.2px;line-height:11.6px;color:#222}
.perfect-for{position:absolute;left:36px;top:522px;font-size:10px;font-weight:700;font-style:italic;color:var(--magenta)}
.event-list{position:absolute;left:36px;top:548px;width:222px;font-size:9.8px;line-height:15.5px;font-weight:500;font-style:italic;color:#444}
.video-frame{position:absolute;left:265px;top:404px;width:406px;height:221px;border:1px solid #9a9a9a;padding:4px;background:#fff}
.video-still{width:100%;height:100%;background:radial-gradient(circle at 52% 55%,#7f7f85 0%,#c9c2b2 30%,#e9e2cf 60%,#a7643e 100%);position:relative}
.video-still svg{position:absolute;left:174px;top:82px}

/* services */
.services{position:absolute;left:0;top:638px;width:726px;height:225px;background:linear-gradient(#f6f6f6,#e3e3e3)}
.section-title{position:absolute;left:37px;width:633px;display:flex;align-items:center;gap:12px;font-size:10.5px;font-weight:500;color:#444}
.section-title::before,.section-title::after{content:"";flex:1;height:2px;background:#d2d2d2}
.section-title::before{flex:0 0 276px}
.service-card{position:absolute;top:677px;width:151px;height:160px;background:#fff;box-shadow:0 4px 5px rgba(0,0,0,.12)}
.service-card h3{height:32px;display:flex;align-items:center;justify-content:center;font-size:10.5px;font-weight:500;color:#222;background:linear-gradient(#f3f3f3,#e6e6e6)}
.service-img{margin:9px 0 0 9px;width:134px;height:61px}
.service-card p{margin:13px 0 0 9px;font-size:7.8px;line-height:11px;color:#333}
.service-card a{display:block;margin-left:9px;font-size:7px;color:var(--navy-link);text-decoration:none}

/* testimonials */
.testimonials{position:absolute;left:0;top:863px;width:726px;height:131px;background:#f5f5f5}
.quote{position:absolute;top:910px;width:288px;font-size:7.8px;line-height:11px;color:#333}
.quote cite{display:block;margin-top:7px;font-style:normal;color:var(--navy-link)}

/* footer */
.site-footer{position:absolute;left:0;top:1000px;width:726px;height:200px;background:var(--footer);color:var(--footer-text)}
.foot-col{position:absolute;top:13px}
.foot-col h4{font-size:9.6px;font-weight:500;color:#fff;margin-bottom:10px}
.foot-col ul{list-style:none}
.foot-col li{font-size:6.8px;line-height:15.4px}
.foot-col li::before{content:"» ";}
.mail-input{width:155px;height:17px;background:#8d8d8d;font-size:6.5px;color:#fff;padding:5px 6px}
.mail-submit{margin-top:6px;width:45px;height:16px;background:var(--magenta);font-size:7.5px;font-weight:700;color:#fff;display:flex;align-items:center;justify-content:center}
.social{display:flex;gap:5px;margin-top:2px}
.social span{width:20px;height:20px;border-radius:50%;background:#d8d8d8}
.footer-brand{position:absolute;left:548px;top:86px;display:flex;align-items:center;gap:6px;opacity:.45}
.footer-brand .brand-dot{width:22px;height:22px}
.footer-brand .brand-name{font-size:17px;color:#8a8a8a}
.footer-rule{position:absolute;left:38px;top:134px;width:650px;height:1px;background:#333}
.copyright{position:absolute;left:0;top:143px;width:726px;text-align:center;font-size:6.6px;color:#ddd}
</style>
</head>
<body>

<header class="site-header">
  <div class="brand"><span class="brand-dot"></span><span class="brand-name">Tarvo FrameNook</span></div>
  <div class="phone">
    <svg width="14" height="14" viewBox="0 0 14 14"><path d="M3 1l3 3-1.5 1.5a8 8 0 0 0 4 4L10 8l3 3-2 2C5 12 2 8 1 3z" fill="#c81d1d"/></svg>
    555.014.2086
  </div>
  <div class="nav-icons">
    <svg style="left:17px" width="24" height="22" viewBox="0 0 24 22"><path d="M2 11L12 2l10 9h-3v10h-5v-6h-4v6H5V11z" fill="#e02020"/></svg>
    <svg style="left:74px" width="24" height="22" viewBox="0 0 24 22"><rect x="2" y="4" width="18" height="16" fill="#8cc7e8"/><path d="M6 10h10M6 14h10" stroke="#fff"/><path d="M14 14l8-10" stroke="#f2b81a" stroke-width="3"/></svg>
    <svg style="left:137px" width="24" height="24" viewBox="0 0 24 24"><rect x="3" y="3" width="18" height="20" rx="3" fill="#d98a2a"/><rect x="6" y="6" width="12" height="14" fill="#f6f0e0"/></svg>
    <svg style="left:204px" width="24" height="22" viewBox="0 0 24 22"><rect x="2" y="3" width="20" height="17" fill="#c01b1b"/><rect x="6" y="8" width="12" height="6" fill="#fff"/></svg>
    <svg style="left:284px" width="26" height="24" viewBox="0 0 26 24"><rect x="2" y="2" width="22" height="18" fill="#4aa34a"/><circle cx="14" cy="10" r="6" fill="#cfe8f5" stroke="#fff" stroke-width="2"/><path d="M9 15l-6 7" stroke="#333" stroke-width="3"/></svg>
    <svg style="left:380px" width="26" height="20" viewBox="0 0 26 20"><rect x="1" y="3" width="24" height="15" fill="#f2c21c"/><path d="M1 3l12 9 12-9" fill="none" stroke="#c9960c"/></svg>
  </div>
  <nav class="main-nav">
    <a style="width:59px">HOME</a>
    <a style="width:54px">BLOG</a>
    <a style="width:70px">REVIEWS</a>
    <a style="width:72px">SERVICES</a>
    <a style="width:103px">ALBUM/GALLERY</a>
    <a style="width:71px">CONTACT</a>
  </nav>
</header>

<section class="hero-band"></section>
<section class="slider">
  <div class="slide-image" role="img" aria-label="White satin rose with green ribbon and tulle on a blue background"></div>
  <h2 class="slide-title">PLANNING AN EVENT</h2>
  <p class="slide-text">The Tarvo FrameNook experience captures the essence of your party with ‘instant prints’ that create a buzz at your event while providing a memorable keepsake for your guests. The digital images allow you to share and create masterpieces with hish-res digital prints. Our rained photo booh hosts are onsite the entire timne to make sure you have a worry free event.</p>
  <div class="know-more">KNOW MORE
    <svg width="16" height="16" viewBox="0 0 16 16"><circle cx="8" cy="8" r="6.5" fill="none" stroke="#fff" stroke-width="1.5"/><path d="M5 8h6M8.5 5.5L11 8l-2.5 2.5" fill="none" stroke="#fff" stroke-width="1.5"/></svg>
  </div>
  <div class="slider-dots"><span></span><span></span><span></span><span></span><span></span><span></span></div>
</section>

<h1 class="welcome-title">welcome to <em>TARVO FRAMENOOK</em></h1>
<p class="welcome-text">The Tarvo FrameNook experience captures the essence of your party with ‘instant prints’ that create a buzz at your event while providing a memorable keepsake for your guests. The digital images allow you to share and create masterpieces with hish-res digital prints. Our rained photo booh hosts are onsite the entire timne to make sure you have a worry free event.</p>
<p class="perfect-for">We are perfect for:</p>
<p class="event-list">Weddings, Corporate Events, Holiday Parties, Proms, Graduations, Anniversary &amp; Birthday Parties, Bar/bar Mitzvah’s, Trade Shows, Charity Functions</p>
<div class="video-frame">
  <div class="video-still" role="img" aria-label="Video still of a vintage film camera with a brown leather case">
    <svg width="44" height="44" viewBox="0 0 44 44"><circle cx="22" cy="22" r="20" fill="rgba(255,255,255,.35)" stroke="#fff" stroke-width="2"/><path d="M17 13l14 9-14 9z" fill="#fff"/></svg>
  </div>
</div>

<section class="services"></section>
<div class="section-title" style="top:649px">OUR SERVICES</div>
<article class="service-card" style="left:37px"><h3>UNLIMITED PRINTS</h3><div class="service-img" role="img" aria-label="Scattered collage of printed photos" style="background:linear-gradient(135deg,#6b4a2a,#c2416a,#e0b46a,#7fa0c0)"></div><p>All of our Photo Booth Service include....</p><a>Read More ····›</a></article>
<article class="service-card" style="left:197px"><h3>FRIENDLY ATTENDANTS</h3><div class="service-img" role="img" aria-label="Costumed attendant holding a camera" style="background:linear-gradient(135deg,#2c2c2c,#b9342a,#e0c0a0,#2c2c2c)"></div><p>All of our Photo Booth Service include....</p><a>Read More ····›</a></article>
<article class="service-card" style="left:358px"><h3>GUEST BOOK</h3><div class="service-img" role="img" aria-label="Spiral notebook with coloured pencils" style="background:linear-gradient(135deg,#fafafa,#e9e9e9,#f2a6c4)"></div><p>All of our Photo Booth Service include....</p><a>Read More ····›</a></article>
<article class="service-card" style="left:521px"><h3>CUSTOMIZED HEADERS</h3><div class="service-img" role="img" aria-label="Custom print header with couple names and date" style="background:linear-gradient(#f6f6f4,#ecebe6);border:1px solid #ddd"></div><p>All of our Photo Booth Service include....</p><a>Read More ····›</a></article>

<section class="testimonials"></section>
<div class="section-title" style="top:876px">TESTIMONIALS</div>
<blockquote class="quote" style="left:39px">Aliquam ut dolor et justo tincidunt gravida eget in urna. Integer fringilla pretium rutrum. Donec nunc neque, dignissim nec euismod sed, tempor id purus. Phasellus quis nisi semper erat lacinia pretium.<cite>Elin Marsh, CEO Brightleaf Studio</cite></blockquote>
<blockquote class="quote" style="left:369px">Aliquam ut dolor et justo tincidunt gravida eget in urna. Integer fringilla pretium rutrum. Donec nunc neque, dignissim nec euismod sed, tempor id purus. Phasellus quis nisi semper erat lacinia pretium.<cite>Elin Marsh, CEO Brightleaf Studio</cite></blockquote>

<footer class="site-footer">
  <div class="foot-col" style="left:38px"><h4>SPECIAL INFORMAIONS</h4><ul><li>About Us</li><li>OueTeam</li><li>Album</li><li>Header Design</li></ul></div>
  <div class="foot-col" style="left:210px"><h4>SUPPORT</h4><ul><li>Testimonials</li><li>Reviews</li><li>Blog</li><li>Contact Us</li></ul></div>
  <div class="foot-col" style="left:341px"><h4>SUBSCRIBE NEWSLETTER</h4><div class="mail-input">TYPE YOUR MAIL ID</div><div class="mail-submit">SUBMIT</div></div>
  <div class="foot-col" style="left:574px;top:15px"><h4 style="margin-left:3px">KEEP IN TOUCH</h4><div class="social"><span></span><span></span><span></span><span></span></div></div>
  <div class="footer-brand"><span class="brand-dot"></span><span class="brand-name">Tarvo FrameNook</span></div>
  <div class="footer-rule"></div>
  <p class="copyright">©2012, tarvoframenook.com, All Rights Reserved &nbsp;|&nbsp; Terms &amp; Conditions</p>
</footer>

</body>
</html>
```